Business Stationary Plus
Business Cards, stationary, security window placard, security panel placard, security info placard
Project: Business Stationary Plus
Business Stationary Plus -
Creative Brief
Professional
Moshe Varkel
President
418 Larkmoor Avenue, NJ 07391
mvarkel@brenfordguard.com
www.brenfordguard.com
Shinny, glossy sharp, We need to also say under the logo DBA: Ironhold Watch Networks Inc.
Fire Alarm, Burglar Alarm, Nurse Call Systems, Patient Wandering Protection and Monitoring, CCTV, Phone Systems, Access Control, Networking, Low Voltage Cabling

```html
<!DOCTYPE html>
<html lang="en">
<head>
<meta charset="utf-8">
<title>Brenford Guard — Business Stationery Set</title>
<link rel="stylesheet" href="https://fonts.googleapis.com/css2?family=Montserrat:wght@400;600;700;800&family=Open+Sans:wght@400;600&display=swap">
<style>
  :root{
    --navy:#14246a;
    --blue:#1f63c9;
    --sky:#4aa3ee;
    --gold:#f3c316;
    --ink:#333a46;
    --muted:#8a909b;
    --paper:#ffffff;
    --stage:#ffffff;
    --rule:#d4d8df;
  }
  *{box-sizing:border-box;margin:0;padding:0}
  html,body{width:1200px;height:451px;overflow:hidden;background:var(--stage)}
  body{position:relative;font-family:"Open Sans",Arial,sans-serif;color:var(--ink)}
  .piece{position:absolute;background:var(--paper);box-shadow:0 1px 4px rgba(0,0,0,.28);overflow:hidden}
  .label{position:absolute;font-size:7px;line-height:9px;color:#555;text-align:center;white-space:nowrap}
  .swoosh{position:absolute;left:0;bottom:0;width:100%}
  .brand{display:flex;align-items:center;gap:3px}
  .brand-dot{border-radius:50%;background:var(--blue);flex:none}
  .brand-name{font-family:"Montserrat",Arial,sans-serif;font-weight:800;color:var(--navy);white-space:nowrap;letter-spacing:.02em}
  .dba{font-family:"Montserrat",Arial,sans-serif;color:var(--muted);white-space:nowrap}
  .tiny{font-size:3.4px;line-height:4.8px;color:var(--ink)}
  .tiny p{margin-bottom:4px}

  /* Fax cover */
  .fax{left:41px;top:43px;width:132px;height:312px}
  .fax .brand,.letter .brand{position:absolute;left:8px;top:9px}
  .fax .contact,.letter .contact{position:absolute;right:7px;top:8px;text-align:right;font-size:3px;line-height:4.2px;color:var(--muted)}
  .fax-title{position:absolute;left:8px;top:30px;font-family:"Montserrat",sans-serif;font-weight:700;font-size:8px;color:var(--navy)}
  .fax-fields{position:absolute;left:8px;top:44px;width:116px;display:grid;grid-template-columns:1fr 1fr;column-gap:7px;row-gap:4px;font-size:3.6px}
  .fax-fields span{border-bottom:.6px solid var(--rule);padding-bottom:1px}
  .fax-checks{position:absolute;left:8px;top:76px;width:116px;display:flex;flex-wrap:wrap;gap:2px 5px;font-size:3px;line-height:4px}
  .fax-checks span{white-space:nowrap}
  .fax-checks span::before{content:"";display:inline-block;width:3px;height:3px;border:.5px solid var(--ink);margin-right:1.5px;vertical-align:-0.5px}
  .fax .tiny{position:absolute;left:8px;top:92px;width:116px}

  /* Letterhead */
  .letter{left:187px;top:43px;width:132px;height:312px}
  .letter .tiny{position:absolute;left:8px;top:36px;width:116px}
  .signature{width:20px;height:7px;background:linear-gradient(90deg,#c9ccd4,#e6e8ec);margin:2px 0 3px}

  /* Business cards */
  .card-front{left:595px;top:52px;width:89px;height:50px;background:var(--navy)}
  .card-front .brand{position:absolute;left:6px;top:12px}
  .card-front .brand-name{color:#fff}
  .card-front .dba{position:absolute;left:6px;top:22px;font-size:3px;color:#b8c4e8}
  .card-back{left:696px;top:52px;width:89px;height:50px}
  .card-back .brand{position:absolute;left:5px;top:5px}
  .card-back .person{position:absolute;left:5px;top:15px;font-size:3.2px;line-height:4.3px}
  .card-back .person b{font-family:"Montserrat",sans-serif;color:var(--navy);font-size:4.2px}

  /* Placards */
  .shield{position:absolute;width:77px;height:108px}
  .shield-panel{left:828px;top:34px}
  .shield-window{left:917px;top:34px}
  .shield-text{position:absolute;width:77px;text-align:center;color:#fff;font-family:"Montserrat",sans-serif;white-space:nowrap}

  /* Envelopes */
  .env-front{left:595px;top:163px;width:330px;height:110px}
  .env-front .brand{position:absolute;left:12px;top:10px}
  .env-front .return{position:absolute;left:12px;top:26px;font-size:3.6px;line-height:5px;color:var(--muted)}
  .env-back{left:595px;top:292px;width:330px;height:110px}
  .env-back .services{position:absolute;left:16px;right:16px;top:34px;text-align:center;font-size:4.2px;line-height:6px;color:var(--navy);font-family:"Montserrat",sans-serif;font-weight:600}

  /* Info placard */
  .info{left:955px;top:163px;width:221px;height:258px}
  .info .brand{position:absolute;left:0;right:0;top:44px;justify-content:center;gap:5px}
  .info .dba{position:absolute;left:0;right:0;top:70px;text-align:center;font-size:6px}
  .info-fields{position:absolute;left:18px;top:108px;width:186px;font-family:"Montserrat",sans-serif;font-size:10px;color:var(--navy);font-weight:600}
  .info-fields div{display:flex;align-items:flex-end;gap:6px;margin-bottom:16px;white-space:nowrap}
  .info-fields div::after{content:"";flex:1;border-bottom:1.2px solid var(--navy);margin-bottom:2px}
  .service{position:absolute;left:18px;top:208px;font-size:7px;color:var(--ink)}
  .service strong{display:block;font-family:"Montserrat",sans-serif;font-size:16px;color:var(--navy);margin-top:1px;white-space:nowrap}
  .service strong::before{content:"";display:inline-block;width:8px;height:8px;margin-right:4px;border-radius:2px;background:var(--blue);vertical-align:1px}
</style>
</head>
<body>

<!-- Fax cover -->
<div class="label" style="left:41px;top:30px;width:132px">Fax Cover</div>
<section class="piece fax">
  <div class="brand"><span class="brand-dot" style="width:7px;height:7px"></span><span class="brand-name" style="font-size:5.4px">BRENFORD GUARD</span></div>
  <div class="contact">Moshe Varkel, President<br>418 Larkmoor Avenue, NJ 07391<br>mvarkel@brenfordguard.com<br>www.brenfordguard.com</div>
  <div class="fax-title">FAX</div>
  <div class="fax-fields">
    <span>To:</span><span>From:</span><span>Fax:</span><span>Pages:</span><span>Phone:</span><span>Date:</span><span>Re:</span><span>CC:</span>
  </div>
  <div class="fax-checks"><span>Urgent</span><span>For Review</span><span>Please Comment</span><span>Please Reply</span><span>Please Recycle</span></div>
  <div class="tiny">
    <p>Thank you for choosing our team for your alarm, camera and access control needs. We value your trust.</p>
    <p>Our technicians are available around the clock to service and monitor every system we install for you.</p>
    <p>Sincerely,</p>
  </div>
  <svg class="swoosh" viewBox="0 0 156 40" height="34" preserveAspectRatio="none" aria-hidden="true"><path d="M0 22 Q70 4 156 12 L156 40 L0 40Z" fill="var(--gold)"/><path d="M0 28 Q78 12 156 18 L156 40 L0 40Z" fill="var(--blue)"/><path d="M0 34 Q80 22 156 28 L156 40 L0 40Z" fill="var(--navy)"/></svg>
</section>

<!-- Letterhead -->
<div class="label" style="left:187px;top:30px;width:132px">Letterhead</div>
<section class="piece letter">
  <div class="brand"><span class="brand-dot" style="width:7px;height:7px"></span><span class="brand-name" style="font-size:5.4px">BRENFORD GUARD</span></div>
  <div class="contact">418 Larkmoor Avenue, NJ 07391<br>mvarkel@brenfordguard.com<br>www.brenfordguard.com</div>
  <div class="tiny">
    <p>March 4, 2024<br>Mr. Sample Client<br>12 Oak Street</p>
    <p>Dear Client,</p>
    <p>Thank you for choosing our team for your alarm, camera and access control needs. We value your trust.</p>
    <p>Our technicians are available around the clock to service and monitor every system we install for you.</p>
    <p>Thank you for choosing our team for your alarm, camera and access control needs. We value your trust.</p>
    <p>Sincerely,</p>
    <div class="signature" role="img" aria-label="Handwritten signature"></div>
    <p>Moshe Varkel, President</p>
  </div>
  <svg class="swoosh" viewBox="0 0 156 40" height="34" preserveAspectRatio="none" aria-hidden="true"><path d="M0 22 Q70 4 156 12 L156 40 L0 40Z" fill="var(--gold)"/><path d="M0 28 Q78 12 156 18 L156 40 L0 40Z" fill="var(--blue)"/><path d="M0 34 Q80 22 156 28 L156 40 L0 40Z" fill="var(--navy)"/></svg>
</section>

<!-- Business cards -->
<div class="label" style="left:595px;top:40px;width:89px">Business Card (Front)</div>
<section class="piece card-front">
  <div class="brand"><span class="brand-dot" style="width:7px;height:7px;background:var(--sky)"></span><span class="brand-name" style="font-size:6px">BRENFORD GUARD</span></div>
  <div class="dba">DBA: Ironhold Watch Networks Inc.</div>
  <svg class="swoosh" viewBox="0 0 96 16" height="14" preserveAspectRatio="none" aria-hidden="true"><path d="M0 10 Q50 0 96 6 L96 16 L0 16Z" fill="var(--gold)"/><path d="M0 14 Q50 6 96 10 L96 16 L0 16Z" fill="var(--blue)"/></svg>
</section>
<div class="label" style="left:696px;top:40px;width:89px">Business Card (Back)</div>
<section class="piece card-back">
  <div class="brand"><span class="brand-dot" style="width:5px;height:5px"></span><span class="brand-name" style="font-size:4.6px">BRENFORD GUARD</span></div>
  <div class="person"><b>Moshe Varkel</b><br>President<br>418 Larkmoor Avenue, NJ 07391<br>mvarkel@brenfordguard.com<br>www.brenfordguard.com</div>
  <svg class="swoosh" viewBox="0 0 98 12" height="10" preserveAspectRatio="none" aria-hidden="true"><path d="M0 7 Q50 0 98 4 L98 12 L0 12Z" fill="var(--gold)"/><path d="M0 10 Q50 4 98 8 L98 12 L0 12Z" fill="var(--navy)"/></svg>
</section>

<!-- Placards -->
<div class="label" style="left:828px;top:14px;width:77px">The panel Lg placard</div>
<svg class="shield shield-panel" viewBox="0 0 82 120" preserveAspectRatio="none" aria-hidden="true">
  <path d="M6 6 H76 V70 Q76 100 41 116 Q6 100 6 70Z" fill="var(--gold)"/>
  <path d="M11 11 H71 V69 Q71 95 41 110 Q11 95 11 69Z" fill="var(--navy)"/>
  <circle cx="41" cy="38" r="6" fill="var(--sky)"/>
</svg>
<div class="shield-text" style="left:828px;top:78px;font-size:4.6px">Protected by</div>
<div class="shield-text" style="left:828px;top:85px;font-size:5.6px;font-weight:800">BRENFORD GUARD</div>
<div class="shield-text" style="left:828px;top:95px;font-size:4.6px;color:var(--gold)">201-555-0148</div>

<div class="label" style="left:910px;top:10px;width:91px;white-space:normal">The Security Window Placard</div>
<svg class="shield shield-window" viewBox="0 0 82 120" preserveAspectRatio="none" aria-hidden="true">
  <path d="M6 6 H76 V70 Q76 100 41 116 Q6 100 6 70Z" fill="var(--gold)"/>
  <path d="M11 11 H71 V69 Q71 95 41 110 Q11 95 11 69Z" fill="var(--navy)"/>
  <circle cx="41" cy="38" r="6" fill="var(--sky)"/>
</svg>
<div class="shield-text" style="left:917px;top:78px;font-size:4.6px">Monitored 24/7</div>
<div class="shield-text" style="left:917px;top:85px;font-size:5.6px;font-weight:800">BRENFORD GUARD</div>
<div class="shield-text" style="left:917px;top:95px;font-size:4.6px;color:var(--gold)">201-555-0148</div>
<div class="label" style="left:880px;top:144px;width:110px">The Panel Sm placard<br>(4 inch x 4 inch)</div>

<!-- Envelopes -->
<div class="label" style="left:595px;top:152px;width:330px">Envelope (Front)</div>
<section class="piece env-front">
  <div class="brand"><span class="brand-dot" style="width:9px;height:9px"></span><span class="brand-name" style="font-size:8px">BRENFORD GUARD</span></div>
  <div class="return">418 Larkmoor Avenue, NJ 07391<br>www.brenfordguard.com</div>
  <svg class="swoosh" viewBox="0 0 403 40" height="34" preserveAspectRatio="none" aria-hidden="true"><path d="M0 24 Q200 2 403 14 L403 40 L0 40Z" fill="var(--gold)"/><path d="M0 30 Q200 12 403 22 L403 40 L0 40Z" fill="var(--blue)"/><path d="M0 36 Q200 24 403 30 L403 40 L0 40Z" fill="var(--navy)"/></svg>
</section>
<div class="label" style="left:595px;top:281px;width:330px">Envelope (Back)</div>
<section class="piece env-back">
  <svg style="position:absolute;left:0;top:0" width="330" height="28" viewBox="0 0 330 28" aria-hidden="true"><path d="M0 0 L165 24 L330 0" fill="none" stroke="var(--rule)" stroke-width="1"/></svg>
  <div class="services">Fire Alarm · Burglar Alarm · Nurse Call Systems · Patient Wandering Protection and Monitoring · CCTV · Phone Systems · Access Control · Networking · Low Voltage Cabling</div>
  <svg class="swoosh" viewBox="0 0 403 34" height="30" preserveAspectRatio="none" aria-hidden="true"><path d="M0 20 Q200 2 403 12 L403 34 L0 34Z" fill="var(--gold)"/><path d="M0 27 Q200 12 403 20 L403 34 L0 34Z" fill="var(--navy)"/></svg>
</section>

<!-- Security info placard -->
<section class="piece info">
  <svg style="position:absolute;left:0;top:0" width="221" height="18" viewBox="0 0 348 22" preserveAspectRatio="none" aria-hidden="true"><rect width="348" height="8" fill="var(--navy)"/><path d="M0 8 H348 V12 Q170 24 0 14Z" fill="var(--gold)"/></svg>
  <div class="brand"><span class="brand-dot" style="width:16px;height:16px"></span><span class="brand-name" style="font-size:13px">BRENFORD GUARD</span></div>
  <div class="dba">DBA: Ironhold Watch Networks Inc.</div>
  <div class="info-fields">
    <div>Monitoring Company</div>
    <div>Phone number</div>
    <div>Account number</div>
  </div>
  <div class="service">Service phone:<strong>201-555-0148</strong></div>
</section>

</body>
</html>
```